Communication and Marketing agency needs a new presentation card

We are a group of communication and marketing agencies specialized in companies that are in the logistics and industrial sector. The head agency is TELVANO Grupo and the group consists of 4 agencies: TELVANO Media, TELVANO Digital, TELVANO Research and DifundeEnPantalla. We hace 4 offices in Spain (Madrid, Barcelona, Valencia and Murcia). We are looking for a clean and attractive design that transmits our experience, brand presence in the market and knowledge to those who receive the card.It has to maintain the colors of the logo that is attached.
Target Market(s)
logistics and industrial sector
Marketing department
Contact Information for Business Card
Clean and attractive design

```html
<!DOCTYPE html>
<html lang="es">
<head>
<meta charset="utf-8">
<title>TELVANO Grupo – Tarjeta de presentación</title>
<link rel="stylesheet" href="https://fonts.googleapis.com/css2?family=Josefin+Sans:wght@600&display=swap">
<style>
  :root {
    --brand-red: #b5202e;
    --brand-red-deep: #a91c29;
    --brand-grey: #636466;
    --band-top: #e3e4e6;
    --band-bottom: #ffffff;
    --white: #ffffff;
  }
  * { margin: 0; padding: 0; box-sizing: border-box; }
  html, body {
    width: 1200px;
    height: 686px;
    overflow: hidden;
    background: var(--white);
  }
  .card {
    position: relative;
    width: 1200px;
    height: 686px;
    font-family: "Josefin Sans", sans-serif;
    font-weight: 600;
  }
  .hero {
    position: absolute;
    inset: 0 0 150px 0;
    background: var(--brand-red);
  }
  .hero-texture {
    position: absolute;
    inset: 0;
    background: radial-gradient(ellipse at center, var(--brand-red) 0%, var(--brand-red-deep) 100%);
  }
  .hero-name {
    position: absolute;
    left: 0;
    right: 0;
    top: 198px;
    text-align: center;
    color: var(--white);
    text-transform: uppercase;
    font-size: 104px;
    line-height: 124px;
    letter-spacing: 2px;
  }
  .hero-name span { display: block; }
  .agencies {
    position: absolute;
    left: 0;
    right: 0;
    bottom: 0;
    height: 150px;
    background: linear-gradient(to bottom, var(--band-top) 0%, var(--band-bottom) 100%);
    display: flex;
    justify-content: space-around;
    align-items: center;
    padding: 0 30px;
  }
  .agency-name {
    width: 250px;
    text-align: center;
    font-size: 30px;
    color: var(--brand-grey);
    letter-spacing: 1px;
  }
  .agency-name.is-red { color: var(--brand-red); }
</style>
</head>
<body>
  <main class="card">
    <section class="hero">
      <div class="hero-texture" role="img" aria-label="Fondo rojo con patrón geométrico de rombos y círculos sutiles"></div>
      <h1 class="hero-name"><span>Difunde</span><span>EnPantalla</span></h1>
    </section>
    <footer class="agencies">
      <p class="agency-name">TELVANO Digital</p>
      <p class="agency-name is-red">TELVANO Media</p>
      <p class="agency-name is-red">TELVANO Grupo</p>
      <p class="agency-name">TELVANO Research</p>
    </footer>
  </main>
</body>
</html>
```